Awesome photographers card for an awesome new business

Double sided business card Black background and silver logo in middle on one side. Details on otherside. please keep it simple

Industry/Entity Type

Photographer

Contact Information for Business Card

Gerald Fenwick
0452817360
GeraldFenwickPhotography47@mailbox.test
www.GeraldFenwickPhotography.test.au
Instagram _Gerald_fenwick

Requirements
Must have
• My logo in Silver
• please use instagram logo instead of "Instagram"

```html
<!DOCTYPE html>
<html lang="en">
<head>
<meta charset="utf-8">
<title>Gerald Fenwick Photography – Business Card</title>
<link rel="stylesheet" href="https://fonts.googleapis.com/css2?family=Open+Sans:wght@300;400;700&display=swap">
<style>
  :root {
    --backdrop: #2a2a2a;
    --card: #f7f7f7;
    --card-front: #111111;
    --ink: #5a5a5a;
    --ink-soft: #7a7a7a;
    --silver: #c4c4c4;
    --silver-soft: #9c9c9c;
    --silver-dark: #8c8c8c;
    --white: #ffffff;
  }
  * { box-sizing: border-box; margin: 0; padding: 0; }
  html, body {
    width: 1200px; height: 900px; overflow: hidden;
    background: var(--backdrop);
    font-family: "Open Sans", Arial, sans-serif;
  }
  .canvas { position: relative; width: 1200px; height: 900px; }
  .card {
    position: absolute; left: 300px; width: 600px; height: 343px;
    background: var(--card); overflow: hidden;
    box-shadow: 0 10px 30px rgba(0,0,0,.5);
  }
  .card--front { top: 88px; background: var(--card-front); }
  .card--back { top: 469px; }

  /* Front */
  .front-name {
    position: absolute; left: 0; right: 0; top: 118px;
    text-align: center; font-weight: 300; font-size: 48px;
    color: var(--silver); letter-spacing: 1px;
  }
  .front-web {
    position: absolute; left: 46px; bottom: 38px;
    font-size: 14px; letter-spacing: 3px; color: var(--silver-soft);
  }

  /* Back */
  .back-band { position: absolute; inset: 0; width: 600px; height: 343px; }
  .back-name {
    position: absolute; right: 28px; top: 30px;
    font-weight: 700; font-size: 17px; color: var(--white);
    text-transform: uppercase;
  }
  .badge {
    position: absolute; left: 70px; top: 140px; width: 112px; height: 112px;
    border: 2px solid var(--silver-dark); border-radius: 50%;
    display: flex; align-items: center; justify-content: center; text-align: center;
    font-weight: 400; font-size: 15px; line-height: 1.25; color: var(--ink-soft);
  }
  .contact-list {
    position: absolute; left: 160px; top: 234px; list-style: none;
    font-size: 15px; line-height: 21px; color: var(--ink);
  }
  .contact-list li { display: flex; align-items: center; gap: 8px; white-space: nowrap; }
  .contact-icon { width: 13px; height: 13px; flex: none; }
</style>
</head>
<body>
<main class="canvas">
  <section class="card card--front" aria-label="Card front">
    <div class="front-name">Gerald Fenwick</div>
    <div class="front-web">www.GeraldFenwickPhotography.test.au</div>
  </section>

  <section class="card card--back" aria-label="Card back">
    <svg class="back-band" viewBox="0 0 600 343" aria-hidden="true">
      <defs>
        <linearGradient id="bandFill" x1="0" y1="0" x2="1" y2="0">
          <stop offset="0" stop-color="#e2e2e2"/>
          <stop offset="0.55" stop-color="#a8a8a8"/>
          <stop offset="1" stop-color="#7c7c7c"/>
        </linearGradient>
      </defs>
      <path d="M0 0 H600 V150 Q360 70 0 120 Z" fill="url(#bandFill)"/>
      <path d="M0 128 Q360 78 600 160" fill="none" stroke="#c9c9c9" stroke-width="3"/>
    </svg>
    <div class="back-name">Gerald Fenwick</div>

    <div class="badge">Gerald<br>Fenwick</div>

    <ul class="contact-list">
      <li>
        <svg class="contact-icon" viewBox="0 0 16 16" aria-hidden="true"><path d="M4 1l3 3-2 2c1 2 3 4 5 5l2-2 3 3-2 3C7 15 1 9 1 3z" fill="#5a5a5a"/></svg>
        0452817360
      </li>
      <li>
        <svg class="contact-icon" viewBox="0 0 16 16" aria-hidden="true"><rect x="1" y="3" width="14" height="10" fill="#5a5a5a"/><path d="M1 3l7 6 7-6" fill="none" stroke="#f7f7f7" stroke-width="1.5"/></svg>
        GeraldFenwickPhotography47@mailbox.test
      </li>
      <li>
        <svg class="contact-icon" viewBox="0 0 16 16" aria-hidden="true"><circle cx="8" cy="8" r="6.5" fill="none" stroke="#5a5a5a" stroke-width="1.6"/><path d="M1.5 8h13M8 1.5c-3 3-3 10 0 13M8 1.5c3 3 3 10 0 13" fill="none" stroke="#5a5a5a" stroke-width="1.2"/></svg>
        www.GeraldFenwickPhotography.test.au
      </li>
      <li>
        <svg class="contact-icon" viewBox="0 0 16 16" aria-hidden="true"><rect x="1" y="1" width="14" height="14" fill="#5a5a5a"/></svg>
        _Gerald_fenwick
      </li>
    </ul>
  </section>
</main>
</body>
</html>
```